Jolly Paws Business Card Update

I have a business card which I love. I want to keep the same logo, colours, font and style. I want to upgrade the scripting and remove some elements and add others.
On the front side under Services - remove the existing wording and insert - Providing individual coaching strategies to create happy, healthy and social canine companions
Under Denise Carvell amend the current wording to read: Qualified in Dog Behavioural Training, Natural Animal Healthcare and Animal Health Science
On the reverse side to remove the web address.

```html
<!DOCTYPE html>
<html lang="en">
<head>
<meta charset="utf-8">
<title>Jolly Paws Business Card</title>
<link href="https://fonts.googleapis.com/css2?family=Open+Sans:ital,wght@0,600;1,400&family=Ubuntu:wght@400;500&family=Arimo:wght@400&display=swap" rel="stylesheet">
<style>
  :root {
    --bg: #2b2b2b;
    --blue-light: #0592cc;
    --blue-mid: #1f5fae;
    --blue-deep: #2b3484;
    --cream: #eee7d2;
    --red: #c4161c;
    --red-dark: #6e1a1e;
    --text-light: #f2f2f2;
    --text-soft: #e4ecf6;
  }
  * { margin: 0; padding: 0; box-sizing: border-box; }
  html, body { width: 1200px; height: 1138px; overflow: hidden; }
  body { background: var(--bg); position: relative; font-family: "Ubuntu", sans-serif; }

  .card {
    position: absolute;
    border-radius: 14px;
    overflow: hidden;
    box-shadow: 0 4px 10px rgba(0,0,0,0.45);
  }

  /* Front */
  .card-front {
    left: 274px; top: 186px; width: 623px; height: 376px;
    background: linear-gradient(180deg, var(--blue-light) 0%, var(--blue-mid) 55%, var(--blue-deep) 100%);
  }
  .front-mark {
    position: absolute; left: 236px; top: 74px; width: 150px; height: 150px;
    border-radius: 50%; background: var(--cream);
  }
  .front-name {
    position: absolute; left: 0; width: 100%; top: 232px; text-align: center;
    font-family: "Open Sans", sans-serif; font-weight: 600; font-size: 36px; line-height: 1;
    color: var(--text-light); letter-spacing: 1px;
  }
  .front-tagline {
    position: absolute; left: 0; width: 100%; top: 276px; text-align: center;
    font-family: "Arimo", sans-serif; font-size: 18px; line-height: 1.1; color: var(--text-soft);
  }
  .front-services {
    position: absolute; left: 90px; width: 443px; top: 310px; text-align: center;
    font-family: "Open Sans", sans-serif; font-style: italic; font-size: 13.5px;
    line-height: 18px; color: var(--text-soft);
  }

  /* Back */
  .card-back {
    left: 276px; top: 608px; width: 618px; height: 374px;
    background: linear-gradient(30deg, var(--blue-deep) 0%, var(--blue-mid) 45%, var(--blue-light) 100%);
  }
  .back-mark {
    position: absolute; left: 63px; top: 84px; width: 168px; height: 168px;
    border-radius: 50%; background: var(--cream);
    display: flex; align-items: center; justify-content: center;
    font-family: "Open Sans", sans-serif; font-weight: 600; font-size: 22px;
    color: var(--blue-deep);
  }
  .holder-name {
    position: absolute; left: 292px; top: 78px;
    font-weight: 500; font-size: 26px; line-height: 30px; color: var(--text-light);
  }
  .holder-quals {
    position: absolute; left: 292px; top: 112px;
    font-family: "Open Sans", sans-serif; font-style: italic; font-size: 15.5px;
    line-height: 21px; color: var(--text-soft);
  }
  .contact-list { position: absolute; left: 296px; top: 190px; list-style: none; }
  .contact-list li {
    display: flex; align-items: center; height: 23px;
    font-size: 17px; color: var(--text-light);
  }
  .contact-list svg { width: 14px; height: 14px; margin-right: 12px; fill: var(--text-light); }
  .mission-band {
    position: absolute; left: 0; bottom: 0; width: 100%; height: 52px;
    background: linear-gradient(90deg, var(--red-dark) 0%, var(--red) 50%, var(--red-dark) 100%);
    display: flex; align-items: center; justify-content: center;
    font-family: "Arimo", sans-serif; font-size: 16.5px; color: var(--text-light);
  }
</style>
</head>
<body>
  <section class="card card-front">
    <div class="front-mark"></div>
    <div class="front-name">JOLLY PAWS</div>
    <div class="front-tagline">HAPPY DOGS, HAPPY OWNERS</div>
    <p class="front-services">Providing individual coaching strategies to create happy, healthy and social canine companions</p>
  </section>

  <section class="card card-back">
    <div class="back-mark">Jolly Paws</div>
    <div class="holder-name">Denise Carvell</div>
    <div class="holder-quals">
      Qualified in Dog Behavioural Training,<br>
      Natural Animal Healthcare and<br>
      Animal Health Science
    </div>
    <ul class="contact-list">
      <li>
        <svg viewBox="0 0 14 14" aria-hidden="true"><path d="M3 0h8v14H3z M4.5 1.5v8h5v-8z M6 11h2v1.5H6z" fill-rule="evenodd"/></svg>
        0412 555 019
      </li>
      <li>
        <svg viewBox="0 0 14 14" aria-hidden="true"><path d="M0 3h14v9H0z"/><path d="M1 4l6 4.5L13 4" stroke="#1f5fae" stroke-width="1.2" fill="none"/></svg>
        jollypaws1@example.com
      </li>
    </ul>
    <div class="mission-band">Promoting communication and connection between dogs and their families</div>
  </section>
</body>
</html>
```